South Florida Real Estate Brokerage Business

The name is LAKE VORISSA REAL ESTATE.
The company is a Real estate realty based in Miami.
Is targeted to Latin American clients.
Must express luxury, and efficiency.
Target clients for properties around 250k to a million +.
Vorissa means Royal in Latin.
Should communicate safety and knowledge of the product and transaction with a tech edge.

The web design needs to be a Social tool, with Friendloop and other media integration of some sort. Needs to have a Show case place, a Search place (MLS listings) with maps and filters.
Needs to reflect luxury but also mixed with a social edge capable of engaging clients or transition them to communicate with the page.
Include the logo from the uploaded files, feel free to change the color or font per webdesign.
This is a Front en design, layout and graphics.
Possible future programming if approved.
I can receive Quotes for the Code part.

Spanish and English speakers living in Latin America and Canada looking for apartments and houses to buy.

Business

• Search area.
Neighbourhood area.
Could be a blog or news area.
Client registration.
Social Plugin
• Social linking to networks.
Log in with friendloop account.
Friendloop Like.

```html
<!DOCTYPE html>
<html lang="en">
<head>
<meta charset="utf-8">
<title>Lake Vorissa Real Estate</title>
<link rel="stylesheet" href="https://fonts.googleapis.com/css2?family=PT+Sans:ital,wght@0,400;0,700;1,400&display=swap">
<style>
  :root{
    --page:#d9d4c9;
    --parchment:#cdb993;
    --parchment-light:#dccaa6;
    --parchment-dark:#b79f74;
    --brown:#6e4b2d;
    --brown-dark:#4e321c;
    --ink:#3a2f26;
    --ink-soft:#5a5048;
    --muted:#7a736b;
    --panel:#ece8e0;
    --band:#cfcabd;
    --bar:#e4e0d6;
    --white:#ffffff;
    --orange:#c8681e;
    --link:#b98a7a;
    --footer:#5a5a5a;
    --footer-dark:#3f3f3f;
    --dot:#2f2f2f;
  }
  *{box-sizing:border-box;margin:0;padding:0}
  html,body{width:1200px;height:2345px;overflow:hidden;background:var(--page)}
  body{font-family:"PT Sans",Arial,sans-serif;color:var(--ink)}
  .canvas{position:relative;width:1200px;height:2345px;overflow:hidden;background:var(--page)}
  .abs{position:absolute}

  /* header */
  .site-header{left:0;top:0;width:1200px;height:160px;background:linear-gradient(180deg,var(--parchment-light),var(--parchment) 60%,var(--parchment-dark))}
  .brand{left:92px;top:14px;width:232px;display:flex;flex-direction:column;align-items:center}
  .brand-mark{width:46px;height:46px;background:var(--ink);margin-bottom:10px}
  .brand-name{font-size:30px;line-height:1;color:var(--ink);text-align:center;white-space:nowrap}
  .brand-name small{display:block;font-size:17px;letter-spacing:2px;margin-top:4px}
  .connect{left:804px;top:84px;font-size:15px;color:var(--ink);display:flex;gap:12px;align-items:center}
  .connect .net{font-size:14px;color:var(--ink);border-bottom:1px solid var(--ink-soft)}

  /* nav */
  .main-nav{left:0;top:160px;width:1200px;height:59px;background:linear-gradient(180deg,var(--brown),var(--brown-dark))}
  .main-nav a{position:absolute;top:18px;color:var(--white);text-decoration:none;font-size:18px}

  /* hero */
  .hero{left:27px;top:219px;width:1146px;height:530px;
    background:
      radial-gradient(ellipse 22% 30% at 62% 12%,#2f6fd0 0%,#4d86d8 45%,rgba(77,134,216,0) 100%),
      radial-gradient(ellipse 30% 22% at 60% 68%,#7ea83a 0%,#4f7a24 45%,rgba(79,122,36,0) 100%),
      radial-gradient(ellipse 18% 30% at 8% 55%,#f2ead6 0%,rgba(242,234,214,0) 100%),
      radial-gradient(ellipse 16% 32% at 90% 55%,#efe5cc 0%,rgba(239,229,204,0) 100%),
      radial-gradient(ellipse 12% 14% at 32% 58%,#f0b862 0%,rgba(240,184,98,0) 100%),
      linear-gradient(180deg,#5a2c14 0%,#8a4a24 18%,#b07a48 45%,#c9a378 72%,#a98a66 100%)}
  .hero-dots{left:938px;top:672px;display:flex;gap:23px}
  .hero-dots span{width:36px;height:36px;border-radius:50%;background:var(--dot)}
  .hero-dots span.active{background:var(--orange)}

  /* search */
  .search-band{left:0;top:766px;width:1200px;height:137px;background:var(--band)}
  .search-bar{left:0;top:782px;width:1200px;height:109px;background:var(--bar)}
  .search-tag{left:27px;top:790px;width:180px;height:92px}
  .search-tag span{position:absolute;left:30px;top:29px;font-size:28px;color:var(--ink)}
  .field-label{font-size:15px;color:var(--ink)}
  .radio{display:flex;align-items:center;gap:10px}
  .radio i{width:13px;height:13px;border:1px solid #777;border-radius:50%;background:var(--white);display:inline-block;position:relative}
  .radio i.on::after{content:"";position:absolute;left:3px;top:3px;width:5px;height:5px;border-radius:50%;background:#222}
  .select{height:22px;background:var(--white);border:1px solid #8a8a8a;display:flex;justify-content:flex-end}
  .select b{width:18px;height:20px;background:#e6e6e6;border-left:1px solid #999;position:relative}
  .select b::after{content:"";position:absolute;left:5px;top:8px;border:4px solid transparent;border-top:5px solid #222}
  .divider{width:1px;height:72px;background:#b8b2a6}
  .search-btn{left:1060px;top:811px;width:104px;height:26px;border-radius:13px;background:linear-gradient(180deg,#d27a34,#a9541b);color:var(--white);font-size:14px;text-align:center;line-height:26px}
  .advanced{left:1068px;top:843px;font-size:11px;color:var(--ink)}

  /* map */
  .section-title{font-size:28px;color:var(--ink);font-weight:400}
  .map{left:27px;top:967px;width:1146px;height:222px;
    background:
      radial-gradient(ellipse 14% 40% at 20% 30%,#b9cf86 0%,rgba(185,207,134,0) 100%),
      radial-gradient(ellipse 16% 45% at 45% 70%,#a9c873 0%,rgba(169,200,115,0) 100%),
      radial-gradient(ellipse 12% 38% at 72% 25%,#c5d894 0%,rgba(197,216,148,0) 100%),
      radial-gradient(ellipse 10% 40% at 88% 70%,#b3cc7e 0%,rgba(179,204,126,0) 100%),
      radial-gradient(ellipse 8% 30% at 60% 45%,#efe4b8 0%,rgba(239,228,184,0) 100%),
      linear-gradient(135deg,#d6dcaa,#ebe5c6 45%,#cfd9a0)}

  /* tiles */
  .tile{width:323px;height:215px;overflow:hidden}
  .tile-photo{position:absolute;inset:0}
  .tile-label{position:absolute;left:0;bottom:0;width:100%;height:52px;background:rgba(92,72,42,.82);color:var(--white);font-size:25px;text-align:center;line-height:52px}
  .intro{left:27px;top:1750px;width:745px;font-size:13.5px;line-height:20px;color:var(--ink-soft)}

  /* sidebar */
  .side-box{left:836px;width:337px;background:var(--panel)}
  .side-head{height:61px;background:linear-gradient(180deg,var(--parchment-light),var(--parchment));display:flex;align-items:center;gap:14px;padding-left:10px}
  .side-head h3{font-size:23px;font-weight:400;color:var(--ink)}
  .side-icon{width:40px;height:36px}
  .post{padding:12px 12px 0 12px}
  .post + .post{padding-top:16px}
  .post h4{font-size:15px;font-weight:400;color:var(--ink)}
  .post .meta{font-size:15px;color:#777;margin-top:8px}
  .post .meta em{font-style:normal;font-size:11px;color:var(--link);text-decoration:underline;margin-left:6px}
  .post p{font-size:13px;line-height:16px;color:var(--muted);margin-top:6px;text-align:justify;hyphens:auto;width:300px}
  .read-more{position:absolute;right:22px;font-size:18px;font-style:italic;color:var(--ink)}
  .news{display:flex;gap:8px;padding:0 10px}
  .news-photo{width:115px;height:80px;flex:none;background:
      radial-gradient(circle at 30% 45%,#d8a27a 0%,rgba(216,162,122,0) 40%),
      radial-gradient(circle at 70% 50%,#b27a54 0%,rgba(178,122,84,0) 45%),
      linear-gradient(135deg,#c89b6e,#7a5238 60%,#b98b5e)}
  .news p{font-size:13px;line-height:23px;color:var(--muted);width:190px;margin-top:-4px}

  /* footer */
  .site-footer{left:0;top:1962px;width:1200px;height:383px;background:linear-gradient(180deg,var(--footer),var(--footer-dark));border-top:6px solid #3a3a3a}
  .footer-title{font-size:24px;color:var(--white);font-weight:400}
  .footer-links{list-style:none}
  .footer-links li{font-size:17px;color:var(--white);line-height:35px}
  .footer-text{font-size:16px;line-height:23.5px;color:var(--white)}
  .input{width:254px;height:32px;background:var(--white);border:1px solid #999}
  .subscribe{left:874px;top:2162px;width:114px;height:40px;border-radius:4px;background:linear-gradient(180deg,#4a4a4a,#262626);color:var(--white);font-size:14px;font-weight:700;text-align:center;line-height:40px}
  .copyright{left:44px;top:2320px;font-size:11px;color:#e6e6e6}
</style>
</head>
<body>
<div class="canvas">

  <header class="abs site-header"></header>
  <div class="abs brand">
    <div class="brand-mark"></div>
    <div class="brand-name">LAKE VORISSA<small>REAL ESTATE</small></div>
  </div>
  <div class="abs connect">GET CONNECTED WITH:
    <span class="net">Friendloop</span><span class="net">Chirpline</span><span class="net">Feed</span>
  </div>

  <nav class="abs main-nav">
    <a style="left:125px">HOME</a>
    <a style="left:219px">COMPANY</a>
    <a style="left:342px">ASSOCIATES</a>
    <a style="left:485px">SEARCH</a>
    <a style="left:606px">PROPERTIES</a>
    <a style="left:751px">MARKETING AND DESIGN</a>
    <a style="left:997px">CONTACT</a>
  </nav>

  <div class="abs hero" role="img" aria-label="Evening courtyard of a luxury villa with wooden beams, white columns, blue sky and a lit tropical garden"></div>
  <div class="abs hero-dots"><span></span><span></span><span class="active"></span></div>

  <section>
    <div class="abs search-band"></div>
    <div class="abs search-bar"></div>
    <svg class="abs search-tag" viewBox="0 0 180 92" aria-hidden="true">
      <polygon points="0,0 150,0 180,46 150,92 0,92" fill="#cbb68e"/>
    </svg>
    <div class="abs search-tag"><span>SEARCH</span></div>

    <div class="abs radio field-label" style="left:242px;top:804px"><i class="on"></i>For Sale</div>
    <div class="abs radio field-label" style="left:242px;top:838px"><i></i>For Rent</div>
    <div class="abs divider" style="left:358px;top:800px"></div>
    <div class="abs field-label" style="left:373px;top:804px">Property Type</div>
    <div class="abs field-label" style="left:373px;top:838px">City Name</div>
    <div class="abs select" style="left:498px;top:803px;width:132px"><b></b></div>
    <div class="abs select" style="left:498px;top:837px;width:132px"><b></b></div>
    <div class="abs divider" style="left:651px;top:800px"></div>
    <div class="abs field-label" style="left:668px;top:804px">Price Min</div>
    <div class="abs field-label" style="left:668px;top:838px">Max Price</div>
    <div class="abs select" style="left:760px;top:803px;width:132px"><b></b></div>
    <div class="abs select" style="left:760px;top:837px;width:132px"><b></b></div>
    <div class="abs divider" style="left:917px;top:800px"></div>
    <div class="abs field-label" style="left:938px;top:804px">Bed</div>
    <div class="abs field-label" style="left:938px;top:838px">Baths</div>
    <div class="abs select" style="left:995px;top:803px;width:36px"><b></b></div>
    <div class="abs select" style="left:995px;top:837px;width:36px"><b></b></div>
    <div class="abs search-btn">SEARCH</div>
    <div class="abs advanced">Advanced Search</div>
  </section>

  <h2 class="abs section-title" style="left:57px;top:922px">SEARCH BY MAP</h2>
  <div class="abs map" role="img" aria-label="Regional road map with towns, highways and a location pin"></div>

  <div class="abs tile" style="left:25px;top:1235px">
    <div class="tile-photo" role="img" aria-label="Two-storey brick family home with a for sale sign on the lawn" style="background:radial-gradient(ellipse 45% 30% at 50% 45%,#c79a5e 0%,rgba(199,154,94,0) 100%),linear-gradient(180deg,#5f97d4 0%,#9cc0e4 25%,#b98c58 48%,#8a6a40 60%,#5d8f38 75%,#4a7a2c 100%)"></div>
    <div class="tile-label">Featured Development</div>
  </div>
  <div class="abs tile" style="left:424px;top:1235px">
    <div class="tile-photo" role="img" aria-label="Grey Victorian style house with a white porch" style="background:radial-gradient(ellipse 40% 32% at 55% 50%,#7d838c 0%,rgba(125,131,140,0) 100%),linear-gradient(180deg,#eef0f2 0%,#d9dcdf 30%,#9aa0a6 55%,#e8e8e6 70%,#5e6b4a 100%)"></div>
    <div class="tile-label">Landlord Shop</div>
  </div>
  <div class="abs tile" style="left:25px;top:1497px">
    <div class="tile-photo" role="img" aria-label="White high-rise apartment towers" style="background:radial-gradient(ellipse 30% 50% at 70% 50%,#f4f3ef 0%,rgba(244,243,239,0) 100%),radial-gradient(ellipse 15% 45% at 10% 45%,#e6e4de 0%,rgba(230,228,222,0) 100%),linear-gradient(180deg,#cfdceb 0%,#bfc3c6 55%,#7d8a66 100%)"></div>
    <div class="tile-label">List your property</div>
  </div>
  <div class="abs tile" style="left:424px;top:1497px">
    <div class="tile-photo" role="img" aria-label="Beige two-storey suburban house under a blue sky" style="background:radial-gradient(ellipse 45% 35% at 45% 55%,#e0cfb0 0%,rgba(224,207,176,0) 100%),radial-gradient(ellipse 20% 30% at 85% 50%,#6d7480 0%,rgba(109,116,128,0) 100%),linear-gradient(180deg,#6ea6dc 0%,#a8c8e6 22%,#d8c7a8 50%,#b8a98e 75%,#8a8070 100%)"></div>
    <div class="tile-label">Video Tour</div>
  </div>

  <p class="abs intro">Lorem Ipsum is simply dummy text of the printing and typesetting industry. Lorem Ipsum has been the industry's standard dummy text ever since the 1500s, when an unknown printer took a galley of type and scrambled it to make a type specimen book. It has survived not only five centuries, but also the leap into electronic typesetting, remaining essentially unchanged. It was popularised in the 1960s with the release of Pressmark sheets containing Lorem Ipsum passages, and more recently with desktop publishing software like Quillset Layout including versions of Lorem Ipsum.</p>

  <aside class="abs side-box" style="top:1235px;height:334px">
    <div class="side-head">
      <svg class="side-icon" viewBox="0 0 40 36" aria-hidden="true">
        <rect x="2" y="14" width="16" height="16" fill="#e0a21a"/><rect x="14" y="2" width="16" height="16" fill="#3a8fd0"/><rect x="20" y="16" width="16" height="16" fill="#5aa83a"/>
      </svg>
      <h3>LATEST TOPIC</h3>
    </div>
    <div class="post">
      <h4>Lorem ipsum dolor sit amet</h4>
      <div class="meta">Thursday, July 26<em>Posted by admin</em></div>
      <p>Lorem ipsum dolor sit amet, consectetur adipiscing elit. Sed blandit massa vel mauris sollicitudin dignissim.</p>
    </div>
    <div class="post">
      <h4>Lorem ipsum dolor sit amet</h4>
      <div class="meta">Thursday, July 26<em>Posted by admin</em></div>
      <p>Lorem ipsum dolor sit amet, consectetur adipiscing elit. Sed blandit massa vel mauris sollicitudin dignissim.</p>
    </div>
    <div class="read-more" style="top:306px">Read more ...</div>
  </aside>

  <aside class="abs side-box" style="top:1602px;height:328px">
    <div class="side-head" style="margin-bottom:21px">
      <svg class="side-icon" viewBox="0 0 40 36" aria-hidden="true">
        <circle cx="20" cy="18" r="15" fill="#3a8fd0"/><circle cx="20" cy="18" r="9" fill="#bfe0f5"/>
      </svg>
      <h3>HOT NEWS</h3>
    </div>
    <div class="news">
      <div class="news-photo" role="img" aria-label="Smiling family group photo"></div>
      <p>Lorem ipsum dolor sit amet, consectetur adipiscing elit. Sed blandit massa vel mauris sollicitudin dign</p>
    </div>
    <div class="news" style="margin-top:28px">
      <div class="news-photo" role="img" aria-label="Smiling family group photo"></div>
      <p>Lorem ipsum dolor sit amet, consectetur adipiscing elit. Sed blandit massa vel mauris sollicitudin dign</p>
    </div>
    <div class="read-more" style="top:289px">Read more ...</div>
  </aside>

  <footer class="abs site-footer"></footer>
  <h3 class="abs footer-title" style="left:55px;top:1996px">NAVIGATION</h3>
  <ul class="abs footer-links" style="left:55px;top:2030px">
    <li>HOME</li><li>COMPANY</li><li>ASSOCIATES</li><li>SEARCH</li><li>PROPERTIES</li><li>MARKETING AND DESIGN</li><li>&nbsp;CONTACT</li>
  </ul>
  <h3 class="abs footer-title" style="left:399px;top:1996px">CONTACT US</h3>
  <p class="abs footer-text" style="left:347px;top:2034px;width:320px">Lorem Ipsum is simply dummy text of the printing and typesetting industry.<br>Lorem Ipsum has been the industry's standard dummy text ever since the 1500s.<br><br>Lorem Ipsum is simply dummy text of the printing and typesetting industry.</p>
  <h3 class="abs footer-title" style="left:873px;top:1996px">NEWSLETTER</h3>
  <div class="abs input" style="left:875px;top:2056px"></div>
  <div class="abs input" style="left:875px;top:2120px"></div>
  <div class="abs subscribe">SUBSCRIBE</div>
  <div class="abs copyright">© Copyright 2011 real estate All Rights Reserved</div>

</div>
</body>
</html>
```